Flyer für Freie Referentin
I thank Korvam Tepesh for the great work! I’am very satisfied with the design of my flyer, with the arrangement of the photos, the font and the colors. Everything is fine and exactly as I imagined before. All my requested changings were changed very quickly and correctly. I would definitely recommend this designer!
Zielgruppe
Ich biete Vorträge, Kurse, Fortbildungen und Privatunterricht an zu den Themen:
Einführung in die Weltreligionen
und
Feste der Religionen
Außerdem biete ich Führungen durch religiöse Gebäude in Berlin an.
Meine Zielgruppen sind:
1. Pädagogen in Kita, Grund-und Oberschule,
2. Religionslehrer,
3.Fachkräfte im interkulturellen Kontext (Ausländerbehörde, Gesundheitswesen, Sozialwesen) und
4. Menschen, die gern reisen und sich für andere Religionen und Kulturen interessieren
Aufgabenstellung
Ich habe selbst einen 6 seitigen Falzflyer entworfen, mit Text und Bildern und würde diesen inhaltlich weitgehend so lassen, und nur in einem ansprechenden Design umgestalten lassen. Die Fotos, die ich liefere, habe ich in den religiösen Gebäuden selbst gemacht.

```html
<!DOCTYPE html>
<html lang="de">
<head>
<meta charset="utf-8">
<title>Weltreligionen Falzflyer</title>
<link href="https://fonts.googleapis.com/css2?family=Kurale&family=Roboto:wght@400;500;700&display=swap" rel="stylesheet">
<style>
:root{
  --red:#8b1d24;
  --red-text:#9b2230;
  --yellow:#fdd35a;
  --yellow-light:#ffdf6e;
  --orange-top:#f6ac24;
  --orange-bottom:#f08d2c;
  --white:#ffffff;
  --ink:#222222;
  --tick:#f8c940;
  --page:#ffffff;
}
*{box-sizing:border-box;margin:0;padding:0}
html,body{width:1200px;height:3600px;overflow:hidden;background:var(--page)}
body{font-family:"Roboto",Arial,sans-serif;color:var(--ink);position:relative}
.spread{position:absolute;left:118px;width:964px;height:680px;overflow:hidden;display:flex}
.spread--outer{top:2019px}
.spread--inner{top:2766px}
.panel{position:relative;width:321.33px;height:100%}
.serif{font-family:"Kurale",Georgia,serif;font-weight:400}

/* outer: about panel */
.panel--about{background:linear-gradient(180deg,var(--orange-top),var(--orange-bottom))}
.portrait{position:absolute;left:40px;top:20px;width:240px;height:320px;border-radius:120px 120px 0 0;background:linear-gradient(180deg,#c98a5a,#6f5a4a 60%,#8d6a3a)}
.about-box{position:absolute;left:20px;right:14px;top:348px;bottom:0;background:var(--red);border-radius:24px 24px 0 0;padding:16px 18px 0;color:var(--white)}
.about-box .kicker{text-align:center;color:var(--yellow);font-size:15px;font-weight:500}
.about-box h2{text-align:center;color:var(--yellow);font-size:31px;margin:4px 0 14px}
.ticks{list-style:none}
.ticks li{position:relative;padding-left:22px;font-size:13.5px;line-height:1.22;margin-bottom:9px}
.ticks li svg{position:absolute;left:0;top:2px;width:14px;height:12px}

/* outer: contact panel */
.panel--contact{background:var(--yellow)}
.band{background:var(--red);color:var(--yellow);text-align:center;font-size:20px;height:32px;line-height:32px}
.contact-band{margin-top:28px}
.contact{text-align:center;font-size:13px;line-height:1.3;padding-top:12px}
.contact .name{font-size:17px;font-weight:500}
.contact .block{margin-top:16px}
.info-band{position:absolute;left:0;right:0;top:254px}
.symbols{position:absolute;left:95px;top:298px;width:132px;height:110px;border-radius:8px;background:rgba(0,0,0,.12)}
.seminar-note{position:absolute;left:40px;right:34px;top:432px;font-weight:700;font-size:13px;line-height:1.25}
.note-box{position:absolute;left:42px;right:38px;background:var(--white);border-radius:12px;box-shadow:3px 4px 6px rgba(0,0,0,.25);text-align:center;font-size:13px;line-height:1.25;padding:8px 10px}
.note-box--prices{top:508px}
.note-box--requests{top:587px}

/* outer: title panel */
.panel--title{background:var(--white)}
.title-block{position:absolute;left:0;right:0;top:0;height:125px;background:var(--red);color:var(--white);text-align:center;padding-top:36px}
.title-block .small{font-size:13px;font-weight:500}
.title-block h1{color:var(--yellow);font-size:28px;line-height:1.1;margin:4px 0 2px}
.title-block .sub{font-size:14px}
.photo{position:absolute;border-radius:10px;box-shadow:2px 3px 0 #f2c04b,3px 5px 6px rgba(0,0,0,.25)}
.footer-block{position:absolute;left:0;right:0;top:550px;bottom:0;background:var(--red);text-align:center;padding-top:20px;color:var(--white)}
.footer-block .religions{color:var(--yellow);font-size:18px;line-height:1.15}
.footer-block p{font-size:14px;margin-top:16px;line-height:1.25}

/* inner */
.top-band{position:absolute;left:0;right:0;top:0;height:24px;background:var(--red);z-index:2}
.bottom-band{position:absolute;left:0;right:0;bottom:0;height:22px;background:var(--red);z-index:2}
.panel--topics{background:var(--white);padding:38px 20px 0}
.panel--visits{background:var(--yellow);padding:42px 34px 0}
.panel--audience{background:var(--white);padding:40px 12px 0 14px}
.heading{color:var(--red-text);font-size:20px;line-height:1.15}
.panel--audience .heading{font-size:21px}
.label{font-weight:700;font-size:14px;margin:12px 0 6px 10px}
.inner-list{list-style:none;margin-left:10px}
.inner-list li{position:relative;padding-left:22px;font-size:13px;line-height:1.22;margin-bottom:6px}
.inner-list li svg{position:absolute;left:0;top:2px;width:14px;height:12px}
.inner-list li.plain{padding-left:22px}
.panel--topics .heading--mid{margin:16px 0 8px}
.topic{font-weight:700;font-size:14px;margin:10px 0 6px}
.topic-list{margin-left:20px}
.panel--visits .heading--mid{margin:22px 0 10px}
.fire{position:absolute;left:0;right:0;top:360px;height:165px;background:radial-gradient(circle at 55% 55%,#f0a030,#a0602a 35%,#3f6a2a 70%,#2c4f20)}
.audience{margin-top:22px}
.audience h3{color:var(--red-text);font-size:15px;font-weight:700;line-height:1.2;margin-bottom:8px}
.audience p{font-size:13px;line-height:1.2;margin-left:22px;margin-bottom:10px}
.audience .item{margin-bottom:14px}
.strip{position:absolute;left:0;top:525px;height:133px;width:964px;display:flex;z-index:1}
.strip > div{height:100%}
.strip-placeholder{background:var(--yellow);color:var(--red-text);font-size:14px;display:flex;align-items:center;justify-content:center}
</style>
</head>
<body>

<svg width="0" height="0" style="position:absolute" aria-hidden="true">
  <defs>
    <symbol id="tick" viewBox="0 0 14 12"><path d="M1 6.5 L5 10.5 L13 1.5" fill="none" stroke="currentColor" stroke-width="2.2" stroke-linecap="round" stroke-linejoin="round"/></symbol>
  </defs>
</svg>

<section class="spread spread--outer">
  <div class="panel panel--about">
    <div class="portrait" role="img" aria-label="Porträtfoto der Referentin vor orangem Hintergrund"></div>
    <div class="about-box">
      <div class="kicker">Über mich:</div>
      <h2 class="serif">Dr. Mara Bretisch</h2>
      <ul class="ticks" style="color:var(--white)">
        <li><svg style="color:var(--tick)"><use href="#tick"/></svg>1992-1999 Studium der Religion­swissenschaft und Indologie in Berlin</li>
        <li><svg style="color:var(--tick)"><use href="#tick"/></svg>2008 Dissertation: „Hindus in der deutschen Diaspora.“</li>
        <li><svg style="color:var(--tick)"><use href="#tick"/></svg>Seit 2000 Wissenschaftliche Refer­entin für Weltreligionen und Hinduis­mus</li>
        <li><svg style="color:var(--tick)"><use href="#tick"/></svg>Seit 2002 Freie Autorin, Schwer­punkt: Religiöse Gruppen in der Diaspora</li>
      </ul>
    </div>
  </div>

  <div class="panel panel--contact">
    <div class="band contact-band serif">Kontakt</div>
    <div class="contact">
      <div class="name">Dr. Mara Bretisch</div>
      <div>Religionswissenschaftlerin und Indologin</div>
      <div class="block">
        <strong>Büro :</strong><br>
        Lindholmer Straße 7 10115 Berlin<br>
        <strong>Tel. :</strong> 030 55501234<br>
        <strong>Mobil :</strong> 0170 5550198<br>
        info@mabretibbe.de<br>
        www.mabretibbe.de
      </div>
    </div>
    <div class="band info-band serif">Mehr Infos &amp; Buchung</div>
    <div class="symbols" role="img" aria-label="Symbole der fünf Weltreligionen"></div>
    <p class="seminar-note">Ich biete Seminare für Einzelpersonen, Bildungseinrichtungen und Teams an – in meinem Büro oder vor Ort.</p>
    <div class="note-box note-box--prices">Aktuelle Preise und Konditionen finden Sie auf meiner Website.<br>www.mabretibbe.de</div>
    <div class="note-box note-box--requests">Individuelle Angebote – Preise auf Nachfrage unter: info@mabretibbe.de oder :Tel.: 03(0) 55501 234</div>
  </div>

  <div class="panel panel--title">
    <div class="title-block">
      <div class="small">Weltreligionen in Berlin erleben</div>
      <h1 class="serif">Vorträge &amp; Seminare</h1>
      <div class="sub">Führungen &amp; Privatunterricht in Berlin</div>
    </div>
    <div class="photo" style="left:43px;top:164px;width:118px;height:116px;background:linear-gradient(160deg,#5a7a3a,#e8e0d0 50%,#b83030)" role="img" aria-label="Foto einer Prozession in weißen Gewändern"></div>
    <div class="photo" style="left:169px;top:164px;width:118px;height:116px;background:linear-gradient(160deg,#2f6a6a,#c84a3a 60%,#e7b070)" role="img" aria-label="Foto einer Zeremonie mit bunten Tüchern"></div>
    <div class="photo" style="left:43px;top:287px;width:118px;height:234px;background:linear-gradient(180deg,#4a8030,#7a9a50 40%,#d0b070 70%,#c04040)" role="img" aria-label="Foto eines Straßenfests mit Tänzern"></div>
    <div class="photo" style="left:169px;top:287px;width:118px;height:115px;background:linear-gradient(160deg,#e0d0b0,#e08a2a 55%,#b0502a)" role="img" aria-label="Foto buddhistischer Mönche"></div>
    <div class="photo" style="left:169px;top:410px;width:118px;height:111px;background:linear-gradient(160deg,#d8d0c0,#4a5060 60%,#303540)" role="img" aria-label="Foto eines Mannes mit Gebetsschal"></div>
    <div class="footer-block">
      <div class="religions serif">Judentum - Christentum - Islam<br>Hinduismus - Buddhismus</div>
      <p>Lernen Sie die Weltreligionen kennen und<br>verstehen!</p>
    </div>
  </div>
</section>

<section class="spread spread--inner">
  <div class="top-band"></div>

  <div class="panel panel--topics">
    <h2 class="heading serif">Weltreligionen verstehen –<br>Menschen besser begegnen</h2>
    <div class="label">Mein Angebot:</div>
    <ul class="inner-list">
      <li><svg style="color:var(--red-text)"><use href="#tick"/></svg>Vorträge &amp; Seminare zu: Judentum, Christentum, Islam, Hinduismus und Buddhismus</li>
      <li><svg style="color:var(--red-text)"><use href="#tick"/></svg>Vorträge &amp; Seminare zu religiösen Festen und Traditionen</li>
      <li><svg style="color:var(--red-text)"><use href="#tick"/></svg>Besuche religiöser Stätten</li>
      <li class="plain">Individuelle Weiterbildungen &amp; Privatunterricht</li>
    </ul>
    <h2 class="heading heading--mid serif">Welche Themen biete ich an?</h2>
    <div class="topic">1. Einführung Weltreligionen</div>
    <ul class="inner-list topic-list">
      <li><svg style="color:var(--red-text)"><use href="#tick"/></svg>Herkunft &amp; Heilige Schrift</li>
      <li><svg style="color:var(--red-text)"><use href="#tick"/></svg>Lehren &amp; Rituale</li>
      <li><svg style="color:var(--red-text)"><use href="#tick"/></svg>Ethik &amp; Verhalten</li>
    </ul>
    <div class="topic">2. Feste in den Religionen</div>
    <ul class="inner-list topic-list">
      <li><svg style="color:var(--red-text)"><use href="#tick"/></svg>Kalender &amp; Anlässe</li>
      <li><svg style="color:var(--red-text)"><use href="#tick"/></svg>Geschichten &amp; Musik</li>
      <li><svg style="color:var(--red-text)"><use href="#tick"/></svg>Rituale &amp; Speisen</li>
    </ul>
  </div>

  <div class="panel panel--visits">
    <h2 class="heading serif">Besuche religiöser Stätten</h2>
    <ul class="inner-list" style="margin:12px 0 0 0">
      <li><svg style="color:var(--red-text)"><use href="#tick"/></svg>Führung durch die Räume</li>
      <li><svg style="color:var(--red-text)"><use href="#tick"/></svg>Teilnahme an Zeremonien</li>
      <li><svg style="color:var(--red-text)"><use href="#tick"/></svg>Austausch mit Gläubigen</li>
    </ul>
    <h2 class="heading heading--mid serif">Was Sie mitnehmen:</h2>
    <ul class="inner-list" style="margin-left:0">
      <li><svg style="color:var(--red-text)"><use href="#tick"/></svg>Klar verständliches Wissen zu den Weltreligionen</li>
      <li><svg style="color:var(--red-text)"><use href="#tick"/></svg>Hintergründe zu Festen, Bräuchen und Symbolen</li>
      <li><svg style="color:var(--red-text)"><use href="#tick"/></svg>Aha-Momente für Beruf, Alltag und Reisen</li>
    </ul>
    <div class="fire" role="img" aria-label="Foto einer Feuerschale bei einer Zeremonie"></div>
  </div>

  <div class="panel panel--audience">
    <h2 class="heading serif">Meine Angebote richten sich an:</h2>
    <div class="audience">
      <div class="item">
        <h3>1.&nbsp; Lehrkräfte allgemein:</h3>
        <p>Gewinnen Sie fundiertes Wissen, um <strong>Schüler*innen unterschiedlicher Herkunft</strong> besser zu begleiten</p>
      </div>
      <div class="item">
        <h3>2.&nbsp; Religionslehrerinnen und<br>&nbsp;&nbsp;&nbsp;&nbsp;&nbsp;Religionslehrer:</h3>
        <p>Vertiefen Sie Ihr Wissen zu Inhalten der großen Religionen – praxisnah und aktuell!</p>
      </div>
      <div class="item">
        <h3>3.&nbsp; Fachkräfte im interkulturellen Kontext</h3>
        <p>(Ausländerbehörde, Asylberatung, Gesundheitswesen)</p>
        <p>Gewinnen Sie Sicherheit im Umgang mit religiös geprägten Verhaltensweisen!</p>
      </div>
      <div class="item">
        <h3>4.&nbsp; Reisefreudige &amp; Neugierige:</h3>
        <p>Entdecken Sie spannende Einblicke in Rituale, Werte und Feiertage weltweit!</p>
      </div>
    </div>
  </div>

  <div class="strip">
    <div style="width:164px;background:linear-gradient(90deg,#3a2a20,#8a6a4a,#4a3a2a)" role="img" aria-label="Foto eines Bücherregals mit alten Schriften"></div>
    <div style="width:155px;background:linear-gradient(180deg,#4a7a3a,#c06a6a 60%,#8a5a4a)" role="img" aria-label="Foto eines Tanzes im Park"></div>
    <div class="strip-placeholder" style="width:196px">photo</div>
    <div style="width:125px;background:linear-gradient(180deg,#2a6ab0,#e0b050 50%,#c07a30)" role="img" aria-label="Foto eines Hindu-Tempelturms"></div>
    <div style="width:147px;background:linear-gradient(180deg,#6a6a6a,#c0b0a0 50%,#5a4a4a)" role="img" aria-label="Foto einer Menschenmenge bei einem Fest"></div>
    <div style="width:177px;background:linear-gradient(180deg,#4a5a7a,#d0d0d8 50%,#3a8aa0)" role="img" aria-label="Foto eines Moscheeinnenraums"></div>
  </div>

  <div class="bottom-band"></div>
</section>

</body>
</html>
```